RTavenor Business Cards & Letterhead

I have a logo but need a design for some new business cards. We are a Design-Build Firm that specializes in the design and construction of commercial projects.
the cards need to be professional. no cartoon stuff.
i would like to have the cards in AI format so I can update the card as needed. Logo is provided.
Our Address is: 4187 Marlowe Ct. Larkfield, West Ardena 27614

```html
<!DOCTYPE html>
<html lang="en">
<head>
<meta charset="utf-8">
<title>RTavenor Business Card</title>
<link href="https://fonts.googleapis.com/css2?family=Open+Sans:wght@400;600;700&display=swap" rel="stylesheet">
<style>
  :root {
    --page: #141518;
    --card: #1f2024;
    --card-edge: #2a2b30;
    --pattern-a: #26272b;
    --pattern-b: #2f3035;
    --brand-blue: #1478c4;
    --text-light: #f2f3f5;
    --text-grey: #8e9096;
    --rule: #9aa0a8;
  }
  * { box-sizing: border-box; margin: 0; padding: 0; }
  html, body {
    width: 1200px; height: 780px; overflow: hidden;
    background: var(--page);
    font-family: "Open Sans", Arial, sans-serif;
  }
  .canvas {
    width: 1200px; height: 780px;
    display: flex; align-items: center; justify-content: center; gap: 40px;
  }
  .card {
    position: relative;
    width: 560px; height: 320px;
    background: var(--card);
    border-radius: 6px;
    box-shadow: 0 18px 40px rgba(0,0,0,.55), inset 0 0 0 1px var(--card-edge);
    overflow: hidden;
  }
  /* back side */
  .card-back__pattern {
    position: absolute; inset: 0;
    background: radial-gradient(circle at 50% 45%, var(--pattern-b), var(--pattern-a) 75%);
  }
  .card-back__wordmark {
    position: absolute; right: 34px; top: 150px;
    display: flex; align-items: center; gap: 10px;
    font-weight: 700; font-size: 32px; letter-spacing: 1px; line-height: 1;
    color: var(--text-grey);
  }
  .brand-square {
    width: 18px; height: 18px; background: var(--brand-blue); border-radius: 2px; flex: none;
  }
  /* front side */
  .card-front__mark {
    position: absolute; left: 0; top: 0; width: 270px; height: 100%;
    display: flex; align-items: center; justify-content: center; gap: 12px;
  }
  .card-front__mark-name {
    font-weight: 700; font-size: 36px; line-height: 1; color: var(--brand-blue);
  }
  .card-front__mark .brand-square { width: 26px; height: 26px; }
  .card-front__divider {
    position: absolute; left: 276px; top: 70px; width: 1px; height: 180px;
    background: linear-gradient(to bottom, transparent, var(--rule) 20%, var(--rule) 80%, transparent);
  }
  .card-front__details {
    position: absolute; left: 298px; top: 58px; right: 16px;
    color: var(--text-light);
  }
  .person-name {
    font-weight: 700; font-size: 20px; letter-spacing: .5px;
    color: var(--brand-blue); text-transform: uppercase; line-height: 1.1;
  }
  .person-title { font-weight: 600; font-size: 14px; margin-top: 2px; }
  .address { font-size: 13px; line-height: 1.45; margin-top: 14px; }
  .contact-list { list-style: none; margin-top: 14px; font-size: 13px; line-height: 1.6; }
  .contact-list li { display: flex; align-items: center; gap: 8px; }
  .contact-icon { width: 14px; height: 14px; flex: none; }
</style>
</head>
<body>
<main class="canvas">
  <section class="card card-back">
    <div class="card-back__pattern" role="img" aria-label="Repeating embossed monogram pattern in dark grey tones"></div>
    <div class="card-back__wordmark">
      <span class="brand-square"></span>
      <span>RTAVENOR</span>
    </div>
  </section>

  <section class="card card-front">
    <div class="card-front__mark">
      <span class="brand-square"></span>
      <span class="card-front__mark-name">RTavenor</span>
    </div>
    <div class="card-front__divider"></div>
    <div class="card-front__details">
      <h1 class="person-name">Rowan Tavenor</h1>
      <p class="person-title">Founder/President</p>
      <p class="address">4187 Marlowe Ct. Larkfield,<br>West Ardena 27614</p>
      <ul class="contact-list">
        <li>
          <svg class="contact-icon" viewBox="0 0 16 16"><circle cx="8" cy="8" r="8" fill="var(--brand-blue)"/><path d="M5.5 4.5l1.5 0 .7 2-1 .8a5 5 0 0 0 2 2l.8-1 2 .7 0 1.5c-3.5.4-6.4-2.5-6-6z" fill="var(--text-light)"/></svg>
          <span>(555) 210-0148</span>
        </li>
        <li>
          <svg class="contact-icon" viewBox="0 0 16 16"><circle cx="8" cy="8" r="8" fill="var(--brand-blue)"/><g fill="none" stroke="var(--text-light)" stroke-width="1"><circle cx="8" cy="8" r="4.5"/><ellipse cx="8" cy="8" rx="2" ry="4.5"/><path d="M3.5 8h9"/></g></svg>
          <span>www.rtavenor.com</span>
        </li>
        <li>
          <svg class="contact-icon" viewBox="0 0 16 16"><circle cx="8" cy="8" r="8" fill="var(--brand-blue)"/><g fill="none" stroke="var(--text-light)" stroke-width="1"><rect x="4" y="5" width="8" height="6"/><path d="M4 5l4 3.5L12 5"/></g></svg>
          <span>RT@RTavenor.com</span>
        </li>
      </ul>
    </div>
  </section>
</main>
</body>
</html>
```